Velvet Riot Rising Line of Sparkling Wine & Spirits

Back info: Nora Beth Quill Owner 555-318-4402 1480 E. Harlow Ave, Bldg. 2, & 3, Ashmere Or. 95871
Sparkling Wines & Memorabilia www.velvetriotrising.com
Ok I have uploaded the winning design. The color that I am after is the Fushia, Raspberry, Red, Matte Satin Matalic Finish. With a 24 Karet Gold color Foil. The Bottle is on the top row and it's the 2nd Bottle in. That is the Color that I want. This is the style of font. Make sure that you put what we're advertising. Good Luck to you all. Warmest regards, Nora
21 & up UniSex
Sparkling Wine and Memorabilia
there listed up above.....

```html
<!DOCTYPE html>
<html lang="en">
<head>
<meta charset="utf-8">
<title>Velvet Riot Rising — Business Card</title>
<link rel="stylesheet" href="https://fonts.googleapis.com/css2?family=Cinzel:wght@400;600&display=swap">
<style>
  :root {
    --stage: #3b3b3d;
    --raspberry: #8e0e48;
    --raspberry-light: #9a1a55;
    --gold: #d0a83f;
    --gold-deep: #b08626;
    --ink-light: #ffffff;
  }
  * { box-sizing: border-box; margin: 0; padding: 0; }
  html, body {
    width: 1200px; height: 1200px; overflow: hidden;
    background: var(--stage);
  }
  .sheet {
    width: 1200px; height: 1200px;
    display: flex; flex-direction: column;
    align-items: center; justify-content: center; gap: 56px;
  }
  .card {
    position: relative;
    width: 880px; height: 520px;
    border-radius: 40px;
    background: linear-gradient(135deg, var(--raspberry) 0%, var(--raspberry-light) 55%, var(--raspberry) 100%);
    border: 3px solid var(--gold-deep);
    overflow: hidden;
    font-family: "Cinzel", serif;
  }

  /* Contact side */
  .rule {
    position: absolute; left: 0; right: 0; height: 5px;
    background: var(--gold);
  }
  .rule--top { top: 54px; }
  .rule--bottom { bottom: 54px; }
  .contact {
    position: absolute; left: 250px; top: 130px;
  }
  .contact__name {
    color: var(--gold); font-size: 44px; font-weight: 400;
    letter-spacing: 1px; line-height: 1;
  }
  .contact__role {
    color: var(--ink-light); font-size: 24px; margin-top: 6px;
  }
  .contact__list { list-style: none; margin-top: 30px; }
  .contact__item {
    display: flex; align-items: flex-start; gap: 16px;
    color: var(--ink-light); font-size: 22px; line-height: 1.2;
    margin-bottom: 12px;
  }
  .contact__icon { width: 26px; height: 26px; flex: none; margin-top: 1px; }

  /* Brand side */
  .card--brand { display: flex; align-items: center; justify-content: center; }
  .brand-name {
    color: var(--gold); font-size: 64px; font-weight: 600;
    letter-spacing: 2px; white-space: nowrap;
  }
</style>
</head>
<body>
<main class="sheet">
  <section class="card card--contact" aria-label="Card back with contact details">
    <div class="rule rule--top"></div>
    <div class="contact">
      <h1 class="contact__name">Nora Beth Quill</h1>
      <p class="contact__role">Owner</p>
      <ul class="contact__list">
        <li class="contact__item">
          <svg class="contact__icon" viewBox="0 0 24 24" aria-hidden="true"><path fill="#d0a83f" d="M6.6 10.8a15.1 15.1 0 0 0 6.6 6.6l2.2-2.2a1 1 0 0 1 1-.25 11.4 11.4 0 0 0 3.6.57 1 1 0 0 1 1 1V20a1 1 0 0 1-1 1A17 17 0 0 1 3 4a1 1 0 0 1 1-1h3.5a1 1 0 0 1 1 1c0 1.250.2 2.450.57 3.570a1 1 0 0 1-.25 1z"/></svg>
          <span>555-318-4402</span>
        </li>
        <li class="contact__item">
          <svg class="contact__icon" viewBox="0 0 24 24" aria-hidden="true"><g fill="none" stroke="#d0a83f" stroke-width="1.8"><circle cx="12" cy="12" r="9.5"/><ellipse cx="12" cy="12" rx="4.2" ry="9.5"/><path d="M2.5 12h19M4 7h16M4 17h16"/></g></svg>
          <span>www.velvetriotrising.com</span>
        </li>
        <li class="contact__item">
          <svg class="contact__icon" viewBox="0 0 24 24" aria-hidden="true"><path fill="#d0a83f" d="M12 2a7 7 0 0 0-7 7c0 5.2 7 13 7 13s7-7.8 7-13a7 7 0 0 0-7-7zm0 9.5A2.5 2.5 0 1 1 12 6.5a2.5 2.5 0 0 1 0 5z"/></svg>
          <span>1480 E. Harlow Ave, Bldg. 2, &amp; 3,<br>Ashmere Or. 95871<br>Sparkling Wines &amp; Memorabilia</span>
        </li>
      </ul>
    </div>
    <div class="rule rule--bottom"></div>
  </section>

  <section class="card card--brand" aria-label="Card front with brand name">
    <p class="brand-name">Velvet Riot Rising</p>
  </section>
</main>
</body>
</html>
```